Redesign of business card for Cedar Ridge Mechanical

We are looking for a new design for our business cards for Cedar Ridge Mechanical. We are a plumbing & HVAC construction company, operating on the West Coast of Canada and USA. Logo attached.
Industry/Entity Type
Construction - Plumbing & HVAC
Contact Information for Business Card
Name, address, phone numbers, email, website address
Look and feel
Each slider illustrates characteristics of the customer's brand and the style your logo design should communicate.

```html
<!DOCTYPE html>
<html lang="en">
<head>
<meta charset="utf-8">
<title>Cedar Ridge Mechanical – Business Card</title>
<link href="https://fonts.googleapis.com/css2?family=Montserrat:wght@400;600;700&display=swap" rel="stylesheet">
<style>
  :root {
    --backdrop: #2a2a2a;
    --card-dark: #1b1b1b;
    --card-dark-alt: #222222;
    --card-light: #f7f7f7;
    --stripe-grey: #8a8a8a;
    --text-light: #ffffff;
    --text-dark: #161616;
    --text-muted: #9a9a9a;
  }
  * { box-sizing: border-box; margin: 0; padding: 0; }
  html, body {
    width: 1200px; height: 963px; overflow: hidden;
    background: var(--backdrop);
    font-family: "Montserrat", sans-serif;
  }
  .canvas {
    width: 1200px; height: 963px;
    display: flex; flex-direction: column; align-items: center; justify-content: center;
    gap: 53px;
  }
  .card {
    width: 700px; height: 400px; border-radius: 22px; overflow: hidden;
    position: relative; box-shadow: 0 10px 30px rgba(0,0,0,.45);
  }

  /* Front side */
  .card-front { background: var(--card-dark); }
  .front-top {
    position: absolute; left: 0; top: 0; width: 100%; height: 176px;
    background: var(--card-light);
    display: flex; align-items: center; justify-content: center;
  }
  .front-stripe {
    position: absolute; left: 0; top: 176px; width: 100%; height: 9px;
    background: var(--stripe-grey);
  }
  .brand-name {
    display: flex; align-items: center; gap: 14px;
    font-weight: 700; font-size: 30px; letter-spacing: 1px; text-transform: uppercase;
  }
  .brand-name .brand-square { width: 22px; height: 22px; background: currentColor; }
  .front-top .brand-name { color: var(--text-dark); }

  .front-info {
    position: absolute; left: 0; top: 185px; width: 100%; height: 215px;
    color: var(--text-light);
  }
  .person {
    position: absolute; right: 380px; top: 45px; text-align: right;
  }
  .person-name { font-weight: 700; font-size: 24px; letter-spacing: 1px; text-transform: uppercase; }
  .person-title { font-size: 17px; margin-top: 2px; }
  .divider {
    position: absolute; left: 340px; top: 40px; width: 1px; height: 78px;
    background: var(--text-light);
  }
  .contacts {
    position: absolute; left: 360px; top: 40px; list-style: none;
    font-size: 19px; line-height: 26px;
  }
  .contacts li { display: flex; align-items: center; gap: 9px; }
  .contacts svg { width: 15px; height: 15px; fill: var(--text-light); flex: none; }
  .address {
    position: absolute; left: 0; width: 100%; top: 140px; text-align: center;
    font-size: 19px;
  }

  /* Back side */
  .card-back {
    background: var(--card-dark);
    display: flex; align-items: center; justify-content: center;
  }
  .card-back .brand-name { color: var(--text-light); font-size: 40px; }
</style>
</head>
<body>
<main class="canvas">
  <section class="card card-front" aria-label="Business card front">
    <div class="front-top">
      <div class="brand-name"><span class="brand-square"></span>Cedar Ridge Mechanical</div>
    </div>
    <div class="front-stripe"></div>
    <div class="front-info">
      <div class="person">
        <div class="person-name">Daniel Hayes</div>
        <div class="person-title">Manager</div>
      </div>
      <div class="divider"></div>
      <ul class="contacts">
        <li>
          <svg viewBox="0 0 24 24" aria-hidden="true"><path d="M6.6 10.8a15.1 15.1 0 0 0 6.6 6.6l2.2-2.2c.3-.3.7-.4 1-.2 1.1.4 2.3.6 3.6.6.6 0 1 .4 1 1V20c0 .6-.4 1-1 1A17 17 0 0 1 3 4c0-.6.4-1 1-1h3.5c.6 0 1 .4 1 1 0 1.3.2 2.5.6 3.6.1.3 0 .7-.2 1z"/></svg>
          123-456-2100
        </li>
        <li>
          <svg viewBox="0 0 24 24" aria-hidden="true"><path d="M2 5h20v14H2zm2 2v.5l8 5 8-5V7zm0 2.8V17h16V9.8l-8 5z"/></svg>
          youremail@example.com
        </li>
        <li>
          <svg viewBox="0 0 24 24" aria-hidden="true"><path d="M12 2a10 10 0 1 0 0 20 10 10 0 0 0 0-20zm6.9 6h-3a15 15 0 0 0-1.3-3.9A8 8 0 0 1 18.9 8zM12 4c.8 1.2 1.5 2.5 1.9 4h-3.8c.4-1.5 1.1-2.8 1.9-4zM4.3 14a8 8 0 0 1 0-4h3.4a16 16 0 0 0 0 4zm.8 2h3a15 15 0 0 0 1.3 3.9A8 8 0 0 1 5.1 16zm3-8h-3a8 8 0 0 1 4.3-3.9A15 15 0 0 0 8.1 8zM12 20c-.8-1.2-1.5-2.5-1.9-4h3.8c-.4 1.5-1.1 2.8-1.9 4zm2.3-6H9.7a14 14 0 0 1 0-4h4.6a14 14 0 0 1 0 4zm.3 5.9a15 15 0 0 0 1.3-3.9h3a8 8 0 0 1-4.3 3.9zm1.7-5.9a16 16 0 0 0 0-4h3.4a8 8 0 0 1 0 4z"/></svg>
          www.yourwebsite.com
        </li>
      </ul>
      <div class="address">Your address, city, state, ZIP 0000</div>
    </div>
  </section>

  <section class="card card-back" aria-label="Business card back">
    <div class="brand-name"><span class="brand-square"></span>Cedar Ridge Mechanical</div>
  </section>
</main>
</body>
</html>
```